Creative, fresh business card design for Ripplecraft Facades

We need a fresh, creative business card design for Ripplecraft Facades. We are the manufacturer of Ripplecraft Facades in Australia. Wall panels are 2400 x 1200mm panels made from MDF and feature 3D patterns on the face of the panel. The colours to be used are green, silver/grey and white RGB
Red 187
Green 207
Blue 65.

An idea is to possibly use a watermark of one of our designs as a background (like on the "Grids" design on the left hand side of page 2 of our brochure).

Target Market(s)

Interior designers, architects, builders and home renovators

Industry/Entity Type

Business

Contact Information for Business Card

Details to go on the card are:
Our logo (attached),
Slogan: "Decorative panels for interiors and exteriors",
Contact name,
Position,
Mobile phone number,
Business address,
Business phone,
Business fax,
Website and
Email address.

I have attached a few images of our panels and our brochure for reference.

The colours of the business card should feature our logo colours which are: RGB
Red 187
Green 207
Blue 65

Requirements
Must have
• Very modern fonts and design. Some of the designs shown especially the "Prisms" design which is a popular design.
Nice to have
• Creative but simple design. Very contemporary.
Should not have
• Anything ornate or old fashioned.

```html
<!DOCTYPE html>
<html lang="en">
<head>
<meta charset="utf-8">
<title>Ripplecraft Facades – Business Card</title>
<link href="https://fonts.googleapis.com/css2?family=Arimo:wght@400;700&display=swap" rel="stylesheet">
<style>
  :root {
    --page-bg: #d8d5cf;
    --card-bg: #f4f5f2;
    --brand-green: #bbcf41;
    --brand-green-dark: #8fae1f;
    --charcoal: #4a4b4d;
    --text-grey: #3f4042;
    --soft-grey: #6e6f72;
  }
  * { box-sizing: border-box; margin: 0; padding: 0; }
  html, body {
    width: 1200px; height: 969px; overflow: hidden;
    background: var(--page-bg);
    font-family: "Arimo", Arial, sans-serif;
  }
  .card {
    position: absolute; left: 100px; top: 200px;
    width: 1000px; height: 568px;
    background: var(--card-bg);
    overflow: hidden;
    box-shadow: 0 10px 30px rgba(0,0,0,.18);
  }
  .card-shapes { position: absolute; inset: 0; width: 100%; height: 100%; }
  .brand {
    position: absolute; left: 46px; top: 52px;
    display: flex; align-items: center; gap: 18px;
  }
  .brand-square { width: 96px; height: 96px; background: var(--brand-green); }
  .brand-name {
    font-size: 36px; font-weight: 400; color: var(--text-grey);
    line-height: 1.1; width: 240px;
  }
  .tagline {
    position: absolute; left: 46px; top: 212px; width: 330px;
    font-size: 19px; letter-spacing: 3.2px; line-height: 1.3;
    color: var(--soft-grey); text-align: center;
  }
  .address {
    position: absolute; left: 46px; top: 306px;
    font-size: 25px; line-height: 32px; color: var(--text-grey);
  }
  .contact-list {
    position: absolute; left: 46px; top: 390px;
    list-style: none; font-size: 25px; color: var(--text-grey);
  }
  .contact-list li { display: flex; align-items: center; height: 38px; }
  .contact-icon { width: 24px; height: 24px; margin-right: 18px; fill: var(--brand-green-dark); }
  .person {
    position: absolute; right: 112px; top: 200px; text-align: right;
  }
  .person-name {
    font-size: 34px; font-weight: 700; color: var(--brand-green-dark);
    letter-spacing: .5px;
  }
  .person-role { font-size: 25px; color: var(--text-grey); margin-top: 4px; }
</style>
</head>
<body>
  <div class="card">
    <svg class="card-shapes" viewBox="0 0 1000 568" preserveAspectRatio="none" aria-hidden="true">
      <rect x="560" y="0" width="440" height="568" fill="var(--brand-green)"/>
      <path d="M0,0 H800 C910,60 955,190 940,285 C915,435 790,530 650,568 H0 Z" fill="var(--charcoal)"/>
      <path d="M0,0 H800 C900,60 935,180 918,255 C885,400 725,520 500,568 H0 Z" fill="var(--card-bg)"/>
    </svg>

    <div class="brand">
      <div class="brand-square"></div>
      <div class="brand-name">Ripplecraft Facades</div>
    </div>
    <p class="tagline">decorative panels for interiors &amp; landscapes</p>

    <p class="address">412 Wattle Grove Road<br>Geelong, Victoria 3220</p>

    <ul class="contact-list">
      <li><svg class="contact-icon" viewBox="0 0 24 24"><path d="M6.6 10.8a15.5 15.5 0 0 0 6.6 6.6l2.2-2.2c.3-.3.7-.4 1-.2 1.1.4 2.3.6 3.6.6.6 0 1 .4 1 1V20c0 .6-.4 1-1 1A17 17 0 0 1 3 4c0-.6.4-1 1-1h3.5c.6 0 1 .4 1 1 0 1.3.2 2.5.6 3.6.1.3 0 .7-.2 1z"/></svg>(555) 214-7730</li>
      <li><svg class="contact-icon" viewBox="0 0 24 24"><path d="M6 3h12v5H6zM3 9h18v9h-3v3H6v-3H3zm5 6v4h8v-4z"/></svg>(555) 214-7731</li>
      <li><svg class="contact-icon" viewBox="0 0 24 24"><path d="M2 5h20v14H2zm2 2v.5l8 5 8-5V7z"/></svg>mhale@ripplecraftfacades.com</li>
      <li><svg class="contact-icon" viewBox="0 0 24 24"><circle cx="12" cy="12" r="10"/></svg>www.ripplecraftfacades.com</li>
    </ul>

    <div class="person">
      <p class="person-name">MARCUS HALE</p>
      <p class="person-role">CEO&amp;Founder</p>
    </div>
  </div>
</body>
</html>
```